Business Card for a Jewellery Brand

Business card for an upscale jewellery brand. Attached is the brand logo and icon and color board. I am looking for two card versions: one for the founder and one is generic. The card should be elegant and convey upscale and premium feel. I am open to both square and rectangle card shapes.

Industry/Entity Type

Jewelry

Contact Information for Business Card

Two cards: (1) Sunela Parvaniya (Founder) (2) General
(1) Sunela Parvaniya card should have Name: Sunela Parvaniya, Title: Founder Email id: sunela@quiremo.com.au. Phone no: +61452913307
(2) Generic card should have Email id: info@quiremo.com.au. Phone no: +61436207518

Requirements
Must have
• Workmark
• ICON
• Phone no
• Email ID
• ABN: 58219740312 (Note: ABN is Business number in Australia)
• Website: www.quiremo.com.au
• Instagram: quiremo_jewellery
• Facebook: @quiremojewellery
Nice to have
• Tagline

```html
<!DOCTYPE html>
<html lang="en">
<head>
<meta charset="utf-8">
<title>Quiremo Business Card</title>
<link rel="stylesheet" href="https://fonts.googleapis.com/css2?family=Lato:wght@400;700&display=swap">
<style>
  :root {
    --page-bg: #e4dfdb;
    --card-bg: #f5f1ef;
    --rose: #c2625f;
    --rose-deep: #b24f4d;
    --rose-soft: #dfa9a4;
    --text-rose: #b6524f;
    --text-muted: #9a5a56;
    --web-text: #f3e6e3;
  }
  * { margin: 0; padding: 0; box-sizing: border-box; }
  html, body {
    width: 1200px; height: 970px; overflow: hidden;
    background: var(--page-bg);
    font-family: "Lato", Arial, sans-serif;
  }
  .card {
    position: absolute; left: 80px; top: 189px;
    width: 1040px; height: 592px;
    background: var(--card-bg);
    overflow: hidden;
    box-shadow: 0 10px 30px rgba(90, 60, 55, 0.18);
  }
  .card-waves { position: absolute; inset: 0; }
  .brand {
    position: absolute; left: 52px; top: 70px; width: 360px;
    display: flex; flex-direction: column; align-items: center;
  }
  .brand-mark {
    width: 130px; height: 130px; border-radius: 50%;
    border: 7px solid var(--rose);
  }
  .brand-name {
    margin-top: 46px;
    font-size: 64px; font-weight: 400; letter-spacing: 10px;
    color: var(--rose); line-height: 1;
  }
  .contact {
    position: absolute; left: 645px; top: 172px;
    color: var(--text-rose);
  }
  .contact-name { font-size: 34px; font-weight: 700; line-height: 1.1; }
  .contact-title { font-size: 25px; color: var(--text-muted); line-height: 1.1; }
  .contact-list { list-style: none; margin-top: 34px; }
  .contact-item {
    display: flex; align-items: center; gap: 8px;
    font-size: 26px; line-height: 37px; color: var(--text-rose);
  }
  .contact-icon { width: 30px; height: 30px; flex: none; }
  .contact-abn { margin-top: 10px; font-size: 27px; color: var(--text-rose); }
  .contact-abn b { font-weight: 700; }
  .website {
    position: absolute; left: 52px; top: 538px;
    font-size: 23px; letter-spacing: 2.5px; color: var(--web-text);
  }
</style>
</head>
<body>
  <div class="card">
    <svg class="card-waves" width="1040" height="592" viewBox="0 0 1040 592" aria-hidden="true">
      <path d="M430 0 C520 40 640 56 800 50 C900 46 980 60 1040 84 L1040 0 Z" fill="var(--rose)"/>
      <path d="M430 0 C520 48 660 72 820 70 C900 69 950 72 950 76 C870 84 720 84 600 66 C520 52 460 24 430 0 Z" fill="var(--rose-soft)"/>
      <path d="M0 436 C120 476 300 486 500 484 C690 482 820 530 880 592 L0 592 Z" fill="var(--rose-soft)"/>
      <path d="M0 452 C130 496 300 505 500 502 C670 500 790 545 830 592 L0 592 Z" fill="var(--rose)"/>
      <path d="M0 520 C160 560 320 570 520 566 C640 564 720 578 760 592 L0 592 Z" fill="var(--rose-deep)" opacity="0.55"/>
    </svg>

    <div class="brand">
      <div class="brand-mark"></div>
      <div class="brand-name">QUIREMO</div>
    </div>

    <div class="contact">
      <div class="contact-name">Sunela Parvaniya</div>
      <div class="contact-title">Founder</div>
      <ul class="contact-list">
        <li class="contact-item">
          <svg class="contact-icon" viewBox="0 0 30 30" aria-hidden="true">
            <circle cx="15" cy="15" r="13" fill="none" stroke="var(--rose)" stroke-width="2"/>
            <path d="M8 13 Q15 7 22 13 L20 15 L18 13 L12 13 L10 15 Z M10 16 H20 V21 H10 Z" fill="var(--rose)"/>
          </svg>
          +61452913307
        </li>
        <li class="contact-item">
          <svg class="contact-icon" viewBox="0 0 30 30" aria-hidden="true">
            <circle cx="15" cy="15" r="13" fill="none" stroke="var(--rose)" stroke-width="2"/>
            <rect x="8" y="10" width="14" height="10" fill="var(--rose)"/>
            <path d="M8 10 L15 16 L22 10" fill="none" stroke="var(--card-bg)" stroke-width="1.5"/>
          </svg>
          sunela@quiremo.com.au
        </li>
        <li class="contact-item">
          <svg class="contact-icon" viewBox="0 0 30 30" aria-hidden="true">
            <circle cx="15" cy="15" r="13" fill="none" stroke="var(--rose)" stroke-width="2"/>
          </svg>
          quiremo_jewellery
        </li>
        <li class="contact-item">
          <svg class="contact-icon" viewBox="0 0 30 30" aria-hidden="true">
            <circle cx="15" cy="15" r="13" fill="none" stroke="var(--rose)" stroke-width="2"/>
          </svg>
          @quiremojewellery
        </li>
      </ul>
      <div class="contact-abn"><b>ABN:</b> 58219740312</div>
    </div>

    <div class="website">www.quiremo.com.au</div>
  </div>
</body>
</html>
```